Banner for promote service of debit card

We are PagoLume and we need the banners to be posted on the facebook and instagram pages.
We want something to communicate that it is an exclusive debit card full of services.
Low commissions.
Our competitors:
https://www.kelmora.example/it/home.html
https://www.zofe.example/it/
https://www.socialpage.example/ostrevabank/
monadrift
maybe some banner that makes the idea of a convenient debit card that everyone can use.
Girls enjoying card shopping.
Please check also website for slogans and phrases to use
https://www.pagolume.example/
Should show the services.
We must convey that it is a fast, simple card that guarantees privacy.
We need strong banners that attract people as these ban will be sponsored on instagram and facebook
People 18-35 y
Open Bank account. low commissions. Easy to use. No limits. 100% Privacy.
- Written in Italian.

```html
<!DOCTYPE html>
<html lang="it">
<head>
<meta charset="utf-8">
<title>PagoLume – Una carta per tutti</title>
<link rel="stylesheet" href="https://fonts.googleapis.com/css2?family=Arimo:wght@700&family=Roboto+Condensed:wght@700&family=Questrial&family=Share+Tech+Mono&display=swap">
<style>
  :root {
    --sky-top: #6ac8e2;
    --sky-bottom: #00a6d2;
    --white: #ffffff;
    --ink: #000000;
    --bag-pink: #f6d3e8;
    --bag-text: #5e5e5e;
    --photo-a: #e9b7a7;
    --photo-b: #d99aa2;
    --card-a: #5c6372;
    --card-b: #323845;
    --card-type: #e6e7ea;
    --card-muted: #a9adb6;
    --brand-grey: #c9ccd2;
    --brand-dot: #e2584a;
    --chip-a: #e6dcb8;
    --chip-b: #b9ad86;
  }
  html, body { margin: 0; padding: 0; overflow: hidden; }
  .banner {
    position: relative;
    width: 1200px;
    height: 1200px;
    overflow: hidden;
    background: linear-gradient(170deg, var(--sky-top) 0%, var(--sky-bottom) 85%);
    font-family: "Arimo", Arial, sans-serif;
    color: var(--white);
  }
  .headline {
    position: absolute;
    left: 86px;
    top: 88px;
    margin: 0;
    font-size: 72px;
    line-height: 66px;
    font-weight: 700;
    letter-spacing: -0.5px;
  }
  .features {
    position: absolute;
    left: 98px;
    top: 276px;
    margin: 0;
    padding: 0;
    list-style: none;
    font-family: "Roboto Condensed", "Arial Narrow", sans-serif;
    font-weight: 700;
    font-size: 40px;
  }
  .features li {
    display: flex;
    align-items: center;
    height: 58.5px;
  }
  .features svg { width: 44px; height: 44px; margin-right: 15px; flex: none; }
  .model-photo {
    position: absolute;
    left: 572px;
    top: 192px;
    width: 560px;
    height: 938px;
    border-radius: 280px 280px 0 0;
    background: radial-gradient(ellipse at 50% 28%, var(--photo-a) 0%, var(--photo-b) 55%, rgba(217,154,162,0) 100%);
    opacity: 0.85;
  }

  /* debit card */
  .debit-card {
    position: absolute;
    left: 85px;
    top: 666px;
    width: 508px;
    height: 304px;
    border-radius: 20px;
    background:
      radial-gradient(ellipse at 55% 45%, rgba(255,255,255,0.08) 0%, rgba(255,255,255,0) 60%),
      linear-gradient(135deg, var(--card-a), var(--card-b));
    transform: rotate(-13deg);
    box-shadow: 0 30px 40px rgba(0,60,90,0.35);
    color: var(--card-type);
  }
  .card-brand {
    position: absolute;
    left: 350px;
    top: 44px;
    display: flex;
    align-items: center;
    gap: 8px;
    font-family: "Arimo", Arial, sans-serif;
    font-weight: 700;
    font-size: 22px;
    color: var(--brand-grey);
  }
  .card-brand-dot {
    width: 22px;
    height: 22px;
    border-radius: 50%;
    background: var(--brand-dot);
  }
  .card-chip {
    position: absolute;
    left: 50px;
    top: 82px;
    width: 84px;
    height: 64px;
    border-radius: 12px;
    background: linear-gradient(135deg, var(--chip-a), var(--chip-b));
  }
  .card-number,
  .card-expiry,
  .card-holder {
    position: absolute;
    margin: 0;
    font-family: "Share Tech Mono", "Courier New", monospace;
    text-shadow: 0 1px 0 rgba(0,0,0,0.45);
    white-space: nowrap;
  }
  .card-number {
    left: 44px;
    top: 160px;
    font-size: 38px;
    letter-spacing: 2.5px;
    word-spacing: 10px;
  }
  .card-expiry {
    left: 240px;
    top: 214px;
    display: flex;
    align-items: center;
    gap: 8px;
    font-size: 24px;
  }
  .card-expiry-label {
    font-family: "Arimo", Arial, sans-serif;
    font-weight: 700;
    font-size: 8px;
    line-height: 10px;
    color: var(--card-muted);
    text-shadow: none;
  }
  .card-code {
    position: absolute;
    left: 48px;
    top: 214px;
    margin: 0;
    font-family: "Arimo", Arial, sans-serif;
    font-weight: 700;
    font-size: 10px;
    color: var(--card-muted);
  }
  .card-holder {
    left: 56px;
    top: 256px;
    font-size: 24px;
    letter-spacing: 3px;
  }

  .bag {
    position: absolute;
    left: 857px;
    top: 714px;
    width: 326px;
    height: 410px;
    background: var(--bag-pink);
  }
  .bag-copy {
    position: absolute;
    left: 881px;
    top: 843px;
    margin: 0;
    font-size: 31px;
    line-height: 43.5px;
    font-weight: 700;
    color: var(--bag-text);
    white-space: nowrap;
  }
  .footer {
    position: absolute;
    left: 0;
    bottom: 0;
    width: 1200px;
    height: 70px;
    background: var(--ink);
    display: flex;
    align-items: center;
    justify-content: center;
    font-family: "Questrial", "Century Gothic", sans-serif;
    font-size: 38px;
    padding-left: 10px;
    box-sizing: border-box;
  }
</style>
</head>
<body>
<main class="banner">
  <h1 class="headline">All in One!<br>Una carta per tutti</h1>

  <ul class="features">
    <li>
      <svg viewBox="0 0 44 44" fill="#fff" aria-hidden="true"><rect x="2" y="4" width="40" height="36" rx="2"/><rect x="6" y="9" width="14" height="12" fill="#43b8dc"/><rect x="6" y="24" width="14" height="12" fill="#43b8dc"/><circle cx="31" cy="22" r="6" fill="#43b8dc"/></svg>
      APRI CONTO BANCARIO
    </li>
    <li>
      <svg viewBox="0 0 44 44" fill="#fff" aria-hidden="true"><rect x="4" y="8" width="4" height="20" rx="2"/><rect x="9" y="4" width="4" height="22" rx="2"/><rect x="14" y="6" width="4" height="20" rx="2"/><path d="M3 26h20v14H6z"/><circle cx="22" cy="30" r="8" fill="#43b8dc" stroke="#fff" stroke-width="3"/><rect x="28" y="2" width="14" height="11" rx="2"/></svg>
      LOW COMMISSIONS
    </li>
    <li>
      <svg viewBox="0 0 44 44" fill="#fff" aria-hidden="true"><circle cx="11" cy="7" r="5"/><circle cx="33" cy="7" r="5"/><path d="M3 16h16v26H3z"/><path d="M25 16h16v26H25z"/><rect x="14" y="22" width="16" height="5"/></svg>
      EASY TO USE
    </li>
    <li>
      <svg viewBox="0 0 44 44" fill="#fff" aria-hidden="true"><ellipse cx="16" cy="7" rx="13" ry="5"/><rect x="3" y="11" width="26" height="7" rx="3"/><rect x="3" y="20" width="26" height="7" rx="3"/><rect x="3" y="29" width="22" height="7" rx="3"/><circle cx="33" cy="34" r="9" stroke="#43b8dc" stroke-width="2"/></svg>
      NO LIMITS
    </li>
    <li>
      <svg viewBox="0 0 44 44" fill="#fff" aria-hidden="true"><path d="M10 30a9 9 0 0 1 1-18 12 12 0 0 1 22 2 8 8 0 0 1 0 16z"/><rect x="15" y="26" width="14" height="14" rx="2" stroke="#43b8dc" stroke-width="2"/><circle cx="22" cy="33" r="2" fill="#43b8dc"/></svg>
      100% PRIVACY
    </li>
  </ul>

  <div class="model-photo" role="img" aria-label="Fotografia di una ragazza sorridente in maglietta rosa che mostra una carta di debito e regge una borsa della spesa"></div>

  <div class="debit-card" role="img" aria-label="Carta di debito PagoLume con chip, numero, scadenza e intestatario">
    <div class="card-brand"><span class="card-brand-dot"></span>PagoLume</div>
    <div class="card-chip"></div>
    <p class="card-number">7867 5678 2364 5978</p>
    <p class="card-code">49576</p>
    <div class="card-expiry"><span class="card-expiry-label">GOOD<br>THRU</span>12/25</div>
    <p class="card-holder">M LUCA FERRI</p>
  </div>

  <div class="bag" aria-hidden="true"></div>
  <p class="bag-copy">Enjoy Your cart !<br>Fai quello che vuoi.<br>Nessur limite<br>Nessun Controllo</p>

  <footer class="footer">www.pagolume.example</footer>
</main>
</body>
</html>
```